KTWG application splash screen

We need a 1024x768 image for use as an application splash screen.
The image will be displayed full screen on an 10 inch industrial PC 1024x768 screen while our application is launching. The image should convey that the application is "Waiting for connection to Wi-Fi access point..." and include a graphic of the industrial PC connected to the access point via an Ethernet cable. A list of troubleshooting steps should be included at the bottom of the image. The troubleshooting steps should not be the main focus of the image and should be shown in a smaller font (but still readable at 1024x768 displayed on a 10 inch screen).
I will include a mock up of the general idea of what we are looking for as well as image files for the industrial PC, a screenshot of our application to show on the PC's screen and the AP.
For general look and feel and a sense of corporate branding please review our website https://marrowgatesoilworks.example/. The splash screen should reflect corporate branding.
Target Market(s)
Users of our application
Industry/Entity Type
Agriculture
Look and feel

```html
<!DOCTYPE html>
<html lang="en">
<head>
<meta charset="utf-8">
<title>KTWG – Waiting for connection</title>
<link rel="stylesheet" href="https://fonts.googleapis.com/css2?family=Poppins:ital,wght@0,400;0,500;0,600;0,700;1,400&display=swap">
<style>
  :root {
    --bg-top: #262626;
    --bg-bottom: #2c2c2c;
    --edge: #4a4a4a;
    --green: #34b36b;
    --white: #ffffff;
    --muted: #e6e6e6;
    --device: #3a3a3a;
    --device-screen: #e9ecea;
    --ap-light: #f4f4f4;
    --ap-shade: #c9c9c9;
    --icon-bg: #0d0d0d;
  }
  * { margin: 0; padding: 0; box-sizing: border-box; }
  html, body { width: 1200px; height: 900px; overflow: hidden; background: var(--bg-top); }
  body { font-family: "Poppins", sans-serif; color: var(--white); }
  .splash { position: relative; width: 1200px; height: 900px; overflow: hidden; background: var(--bg-top); }

  .backdrop { position: absolute; inset: 0; }

  .brand { position: absolute; left: 45px; top: 34px; }
  .brand-name { font-size: 60px; font-weight: 700; line-height: 1; letter-spacing: 2px; color: var(--white); }
  .brand-company { margin-top: 12px; font-size: 21px; font-weight: 400; color: var(--green); line-height: 1.1; }
  .brand-rule { width: 196px; height: 2px; background: var(--white); margin-top: 4px; }

  .headline { position: absolute; left: 440px; width: 520px; top: 70px; text-align: center;
    font-size: 58px; font-weight: 600; line-height: 82px; }
  .headline .accent { color: var(--green); }
  .headline .wide { display: block; margin-left: -60px; margin-right: -80px; }

  .cab-computer { position: absolute; left: 59px; top: 307px; width: 267px; height: 211px;
    border-radius: 12px; background: linear-gradient(180deg, #4a4a4a, var(--device)); }
  .cab-computer .screen { position: absolute; left: 20px; top: 18px; right: 20px; bottom: 40px;
    border-radius: 4px; background: linear-gradient(180deg, var(--device-screen), #cfe9d9); }

  .access-point { position: absolute; left: 1040px; top: 209px; width: 57px; height: 236px;
    border-radius: 8px; background: linear-gradient(90deg, var(--ap-shade), var(--ap-light) 45%, var(--ap-shade)); }

  .link { position: absolute; inset: 0; }

  .label { position: absolute; font-size: 21px; font-weight: 500; text-align: center; white-space: nowrap; }
  .label .accent { color: var(--green); }
  .label-computer { left: 190px; top: 533px; transform: translateX(-50%); }
  .label-cable { left: 680px; top: 442px; transform: translateX(-50%); }
  .label-ap { left: 1064px; top: 512px; transform: translateX(-50%); }
  .label-model { left: 1064px; top: 543px; transform: translateX(-50%); font-size: 16px; color: var(--green); font-weight: 500; }

  .app-icon { position: absolute; left: 123px; top: 711px; width: 129px; height: 129px; border-radius: 24px;
    background: var(--icon-bg); display: flex; align-items: center; justify-content: center;
    font-size: 34px; font-weight: 700; color: var(--white); letter-spacing: 1px; }

  .troubleshooting { position: absolute; left: 543px; top: 668px; width: 620px; }
  .troubleshooting h2 { font-size: 20px; font-weight: 600; margin-bottom: 18px; }
  .troubleshooting ul { list-style: none; font-size: 15px; line-height: 22.5px; color: var(--muted); }
  .troubleshooting li { position: relative; padding-left: 12px; }
  .troubleshooting li::before { content: "•"; position: absolute; left: 0; }
  .troubleshooting ul ul { margin-left: 44px; }
  .troubleshooting ul ul li { padding-left: 16px; }
  .troubleshooting ul ul li::before { content: "◦"; }
</style>
</head>
<body>
<main class="splash">
  <svg class="backdrop" width="1200" height="900" viewBox="0 0 1200 900" aria-hidden="true">
    <polygon points="0,640 674,600 1200,640 1200,900 0,900" fill="var(--bg-bottom)"/>
    <polyline points="0,640 674,600 1200,640" fill="none" stroke="var(--edge)" stroke-width="3"/>
    <polygon points="0,630 404,630 480,900 0,900" fill="var(--green)"/>
  </svg>

  <header class="brand">
    <div class="brand-name">KTWG</div>
    <div class="brand-company">Marrowgate Soil Works Inc.</div>
    <div class="brand-rule"></div>
  </header>

  <h1 class="headline">
    <span>Waiting for</span><br>
    <span>connection to</span><br>
    <span class="accent wide">Wi-Fi access point...</span>
  </h1>

  <svg class="link" width="1200" height="900" viewBox="0 0 1200 900" aria-hidden="true">
    <polyline points="350,490 1068,490 1068,455" fill="none" stroke="var(--green)" stroke-width="3"/>
    <rect x="334" y="482" width="20" height="16" rx="2" fill="var(--green)"/>
    <rect x="1060" y="445" width="16" height="20" rx="2" fill="var(--green)"/>
  </svg>

  <div class="cab-computer" role="img" aria-label="Industrial tractor cab computer showing the seeding application screen">
    <div class="screen"></div>
  </div>

  <div class="access-point" role="img" aria-label="Outdoor Wi-Fi access point with two antennas"></div>

  <div class="label label-computer">Tractor cab <span class="accent">computer</span></div>
  <div class="label label-cable">Ethernet <span class="accent">cable</span></div>
  <div class="label label-ap">Wi-Fi Access Point</div>
  <div class="label label-model">Ridgeline AP-220 Outdoor</div>

  <div class="app-icon">KTWG</div>

  <section class="troubleshooting">
    <h2>Troubleshooting steps:</h2>
    <ul>
      <li>This screen should only be visible for a short time on boot.</li>
      <li>If this screen stays visible for more than a minute:
        <ul>
          <li>Verify that when the cab computer is powered up the Wi-Fi Access Point (AP) is also powered up (indicated by green light on side of the AP).</li>
          <li>Check the Ethernet cable for damage and replace if damaged.</li>
          <li>Contact KTWG support for further assistance.</li>
        </ul>
      </li>
    </ul>
  </section>
</main>
</body>
</html>
```